Local fast-growing company in the service sector

We are looking for a modern business card design, which should also appear on our letterheads

Target Market(s)

Private and industrial sectors

Contact Information for Business Card

Vorname Name
Kellberger Str. 18
73614 Schorndorf
Tel.: 07146-839214-0
Name@agentur-kvtl.de

Colors
9d9d9d
919191
aaaaaa

Requirements
Must have
• The logo (file) in silver

```html
<!DOCTYPE html>
<html lang="de">
<head>
<meta charset="utf-8">
<title>KVTL – Visitenkarte</title>
<link rel="stylesheet" href="https://fonts.googleapis.com/css2?family=Roboto:wght@300;400;700&display=swap">
<style>
  :root {
    --page-bg: #d9d6d1;
    --card-black: #0b0b0b;
    --card-sheen: #2a2a2a;
    --silver-light: #e4e4e4;
    --silver-mid: #aaaaaa;
    --silver-dark: #919191;
    --silver-text: #9d9d9d;
    --ink-dark: #2b2b2b;
    --white: #f4f4f4;
  }
  * { margin: 0; padding: 0; box-sizing: border-box; }
  html, body { width: 1200px; height: 1023px; overflow: hidden; }
  body {
    background: var(--page-bg);
    font-family: "Roboto", Arial, sans-serif;
    position: relative;
  }
  .card {
    position: absolute;
    left: 250px;
    width: 700px;
    height: 400px;
    border-radius: 16px;
    background: linear-gradient(135deg, var(--card-sheen) 0%, var(--card-black) 45%, var(--card-black) 100%);
    box-shadow: 0 10px 30px rgba(0,0,0,.35);
    overflow: hidden;
    color: var(--white);
  }
  .card--front { top: 90px; }
  .card--back { top: 533px; }

  /* Front */
  .name-band {
    position: absolute;
    left: 0; top: 118px;
    width: 340px; height: 90px;
    background: linear-gradient(90deg, var(--silver-mid) 0%, var(--silver-light) 55%, var(--silver-light) 100%);
    padding: 18px 0 0 34px;
  }
  .person-name {
    font-weight: 700;
    font-size: 27px;
    letter-spacing: .5px;
    color: var(--ink-dark);
    line-height: 1;
  }
  .person-title {
    margin-top: 8px;
    font-size: 13px;
    letter-spacing: 1.5px;
    color: #555;
  }
  .brand {
    position: absolute;
    display: flex;
    align-items: center;
    gap: 14px;
  }
  .brand__mark {
    width: 22px; height: 22px;
    background: var(--silver-mid);
  }
  .brand__name {
    font-weight: 700;
    color: var(--silver-light);
    line-height: 1;
  }
  .card--front .brand { left: 362px; top: 126px; }
  .card--front .brand__name { font-size: 64px; }
  .brand-url {
    position: absolute;
    left: 398px; top: 196px;
    font-size: 17px;
    font-weight: 300;
    letter-spacing: 1px;
    color: var(--silver-text);
  }
  .contacts {
    position: absolute;
    left: 34px; bottom: 36px;
    list-style: none;
    font-size: 19px;
    font-weight: 300;
    color: var(--white);
  }
  .contacts li { display: flex; align-items: center; gap: 12px; line-height: 1.45; }
  .contacts svg { width: 14px; height: 14px; fill: none; stroke: var(--silver-mid); stroke-width: 1.6; }

  /* Back */
  .card--back .brand { left: 60px; top: 240px; }
  .card--back .brand__name { font-size: 56px; }
  .card--back .brand-url { left: 96px; top: 303px; font-size: 15px; }
  .address {
    position: absolute;
    right: 40px; top: 42px;
    text-align: right;
    font-size: 19px;
    font-weight: 300;
    font-style: normal;
    line-height: 1.45;
    color: var(--white);
  }
</style>
</head>
<body>

<section class="card card--front" aria-label="Vorderseite">
  <div class="name-band">
    <p class="person-name">MAREK LINDQVIST</p>
    <p class="person-title">DIRECTOR</p>
  </div>
  <div class="brand">
    <span class="brand__mark"></span>
    <span class="brand__name">KVTL</span>
  </div>
  <p class="brand-url">agentur-kvtl.de</p>
  <ul class="contacts">
    <li>
      <svg viewBox="0 0 14 14" aria-hidden="true"><path d="M3 1.5 L5 1.5 L6 4.5 L4.5 5.5 Q5.5 8.5 8.5 9.5 L9.5 8 L12.5 9 L12.5 11 Q12 12.5 10.5 12.5 Q2 11.5 1.5 3.5 Q1.5 1.5 3 1.5 Z"/></svg>
      07146-839214-0
    </li>
    <li>
      <svg viewBox="0 0 14 14" aria-hidden="true"><rect x="1.5" y="3" width="11" height="8.5"/><path d="M1.5 3 L7 7.5 L12.5 3"/></svg>
      Name@agentur-kvtl.de
    </li>
  </ul>
</section>

<section class="card card--back" aria-label="Rückseite">
  <address class="address">
    Kellberger Str. 18<br>
    73614 Schorndorf
  </address>
  <div class="brand">
    <span class="brand__mark"></span>
    <span class="brand__name">KVTL</span>
  </div>
  <p class="brand-url">agentur-kvtl.de</p>
</section>

</body>
</html>
```